Supplement Brand Product Labels

Product Label for Supplement Brand

Protein Powder Label (2 x different flavours)

Neon Colours / Skull / Spooky
Refer to pictures below, they are the look we are wanting to go with but put our touch to it aswell.

Target Market(s)

Fitness

Industry/Entity Type

Supplement Brand

Colors
0054AA
0677BA
7BADD7
CADEEF
E8F1F8
0094D4
00A9DD
6FCCEA
C7EBF8
E9F6FB
00AB8E
00BBA5
67D7C9
C6EFE9
E9F9F6
59FF00
82FF00
B8FF75
E3FFCB
F4FFEA
FFF300
FFF600
FEFA6F
FFFEC7
FFFEE8
FFC000
F8CF3A
FAE287
FDF2CF
FEFAEE
F0912C
F2A743
F7CA91
FBE8D2
FDF5EE
EE7325
F08F49
F5BC92
FAE3D3
FDF4ED
EB3D1F
EC4F4E
F09395
F8D3D4
FCEDEE
E54698
E96AAD
F1A4CE
F9D9EA
FCEFF6
A7469A
B969AE
D3A5CF
EDDBEB
F8F0F9
6B429C
8869AF
B7A5CE
E3DAEB
F3F0F8

Requirements
Nice to have
• Skull, Neon Colours, Abstract, Barbell, Lighting Bolt, Flames, Spooky

```html
<!DOCTYPE html>
<html lang="en">
<head>
<meta charset="utf-8">
<title>Grimforge Titan Protein – Choco Fudge Label</title>
<link href="https://fonts.googleapis.com/css2?family=Lato:wght@400;700;900&family=Oswald:wght@700&family=Baloo+2:wght@700&display=swap" rel="stylesheet">
<style>
  :root{
    --page:#ffffff;
    --label:#050505;
    --ink:#ffffff;
    --neon-green:#59ff00;
    --leaf-green:#3fae2a;
    --deep-green:#1f6e16;
    --bone:#eeeeee;
    --neon-pink:#e54698;
    --purple:#6b429c;
    --magenta:#a7469a;
    --red:#eb3d1f;
    --orange:#f0912c;
    --yellow:#fff300;
    --green:#59c000;
    --teal:#00bba5;
  }
  *{box-sizing:border-box;margin:0;padding:0}
  html,body{width:1200px;height:1049px;overflow:hidden;background:var(--page)}
  body{position:relative;font-family:"Lato",sans-serif;color:var(--ink)}

  .label{position:absolute;left:50px;top:336px;width:1107px;height:393px;background:var(--label);overflow:hidden}

  .skull-art{position:absolute;top:0;height:393px;opacity:.8}
  .skull-art--left{left:0;width:290px;
    background:linear-gradient(165deg,var(--purple) 0%,var(--magenta) 16%,var(--red) 32%,var(--orange) 46%,var(--yellow) 58%,var(--green) 76%,var(--teal) 96%);
    -webkit-mask-image:linear-gradient(90deg,#000 70%,transparent 100%);
    mask-image:linear-gradient(90deg,#000 70%,transparent 100%)}
  .skull-art--right{right:0;width:300px;
    background:linear-gradient(195deg,var(--purple) 0%,var(--magenta) 16%,var(--red) 34%,var(--orange) 50%,var(--yellow) 62%,var(--green) 78%,var(--teal) 96%);
    -webkit-mask-image:linear-gradient(270deg,#000 65%,transparent 100%);
    mask-image:linear-gradient(270deg,#000 65%,transparent 100%)}

  .directions{position:absolute;left:26px;top:38px;width:191px;font-size:6.8px;line-height:10.2px}
  .directions h2{font-weight:400;font-size:9.4px;line-height:12px;margin-bottom:1px}
  .directions p{margin-bottom:10px;text-align:justify}
  .directions .storage{font-weight:700}

  .maker{position:absolute;left:26px;top:222px}
  .maker-name{display:flex;align-items:center;gap:4px;font-weight:900;font-size:19px;line-height:22px}
  .maker-name .dot{width:10px;height:10px;border-radius:50%;background:var(--ink)}
  .maker-contact{font-size:5.6px;line-height:7px;margin-top:4px}
  .maker-contact strong{font-weight:700}
  .batch-box{position:absolute;left:26px;top:280px;width:123px;height:74px;background:var(--ink)}

  .brand-name{position:absolute;left:511px;top:30px;transform:translateX(-50%);white-space:nowrap;font-weight:900;font-size:50px;line-height:60px;letter-spacing:1px}
  .product-title{position:absolute;left:365px;top:112px;width:295px;text-align:center;font-family:"Oswald",sans-serif;font-weight:700;font-size:44px;line-height:60px;color:var(--ink);text-shadow:2px 2px 0 var(--neon-pink);white-space:nowrap}
  .hero-art{position:absolute;left:307px;top:168px;width:418px;height:162px;
    border-radius:50% 50% 30% 30% / 70% 70% 30% 30%;
    background:linear-gradient(90deg,transparent 0%,var(--leaf-green) 8%,var(--deep-green) 30%,var(--bone) 40%,var(--bone) 60%,var(--deep-green) 70%,var(--leaf-green) 92%,transparent 100%)}
  .flavour{position:absolute;left:511px;top:331px;transform:translateX(-50%) rotate(-3deg);font-family:"Baloo 2",sans-serif;font-weight:700;font-size:22px;line-height:26px;white-space:nowrap}
  .net-weight{position:absolute;left:666px;top:337px;width:37px;height:20px;background:var(--ink);color:var(--label);font-weight:900;font-size:14px;line-height:20px;text-align:center}

  .nutrition{position:absolute;left:759px;top:38px;width:205px;border-collapse:collapse;font-size:6.8px}
  .nutrition th{font-weight:700;font-size:5.4px;line-height:6.5px;text-align:left;vertical-align:top;padding-bottom:8px}
  .nutrition th.num,.nutrition td.num{text-align:right;padding-right:4px}
  .nutrition td{height:21.2px;vertical-align:middle}
  .nutrition .indent{padding-left:5px}

  .ingredients{position:absolute;left:762px;top:215px;width:199px;font-size:6.8px;line-height:10.2px}
  .ingredients h3,.allergens h3{font-weight:400;font-size:11px;line-height:14px;margin-bottom:2px}
  .allergens{position:absolute;left:762px;top:292px;font-size:6.8px;line-height:10px}
  .origin-badge{position:absolute;left:763px;top:336px;width:82px;height:18px;border-radius:3px;background:var(--ink)}

  .amino{position:absolute;left:979px;top:40px;width:103px;border-collapse:collapse;font-size:6.8px}
  .amino caption{font-size:8.4px;text-align:left;padding-left:4px;padding-bottom:2px;border-bottom:1px solid var(--ink)}
  .amino th{font-size:5.6px;font-weight:700;text-align:left;padding:2px 0 3px;border-bottom:1px solid var(--ink)}
  .amino th.num{text-align:right}
  .amino td{height:16.15px;vertical-align:middle}
  .amino .num{text-align:right}
</style>
</head>
<body>
<main class="label">
  <div class="skull-art skull-art--left" role="img" aria-label="Stacked neon rainbow skull illustrations"></div>
  <div class="skull-art skull-art--right" role="img" aria-label="Stacked neon rainbow skull illustrations"></div>

  <section class="directions">
    <h2>Directions Of Use</h2>
    <p>Mix 1 heaped scoop (40 grams) with 250ml of water or milk and consume immediately. Consume 1 - 2 times per day when required.</p>
    <p>Formulated supplementary sports food. Not suitable for children under 15 years of age or pregnant women. Should only be used under medical or dietetic supervision. This product is not a sole source of nutrition and should be consumed in conjunction with a nutritious diet and appropriate physical training or exercise program.</p>
    <p class="storage">Store in a cool dry place out of direct sunlight.</p>
  </section>

  <section class="maker">
    <div class="maker-name"><span class="dot"></span>KVN</div>
    <div class="maker-contact"><strong>www.kestrelvalenutrition.com</strong><br>42 Harbour Lane, Southport, QLD 4215</div>
  </section>
  <div class="batch-box"></div>

  <div class="brand-name">GRIMFORGE</div>
  <h1 class="product-title">TITAN PROTEIN</h1>
  <div class="hero-art" role="img" aria-label="Winged skull illustration in green and bone white"></div>
  <div class="flavour">Choco Fudge</div>
  <div class="net-weight">1KG</div>

  <table class="nutrition">
    <thead>
      <tr><th>25 Serving Per 1kg Packet<br>40 grams Per Serve</th><th class="num">Average Quantity<br>Per Serving</th><th class="num">Average Quantity<br>Per 100g</th></tr>
    </thead>
    <tbody>
      <tr><td>Energy (KJ)</td><td class="num">618</td><td class="num">1545</td></tr>
      <tr><td>Protein (G)</td><td class="num">30</td><td class="num">74.9</td></tr>
      <tr><td>Fat, Total (G)</td><td class="num">1.6</td><td class="num">4.1</td></tr>
      <tr><td class="indent">(Saturated) (G)</td><td class="num">0.7</td><td class="num">1.8</td></tr>
      <tr><td>Carbohydrates (G)</td><td class="num">3.3</td><td class="num">8.2</td></tr>
      <tr><td class="indent">(Sugar) (G)</td><td class="num">1.1</td><td class="num">2.8</td></tr>
      <tr><td>Sodium (MG)</td><td class="num">88</td><td class="num">220</td></tr>
    </tbody>
  </table>

  <section class="ingredients">
    <h3>Ingredients</h3>
    <p>Grass-Fed Whey Protein Concentrate, Grass-Fed Milk Protein Isolate, Grass-Fed Whey Protein Isolate, Flavour, Cocoa, L-Leucine, L-Glutamine, β-Hydroxy β-methylbutyric Acid, Iceland Sea Minerals (Lithothamnion species, E296, E330), Lactase Enzyme, Sweetener 955.</p>
  </section>
  <section class="allergens">
    <h3>Allergens</h3>
    <p>Dairy, Soy.</p>
  </section>
  <div class="origin-badge"></div>

  <table class="amino">
    <caption>Typical Amino Acid Profile</caption>
    <thead><tr><th>Amino Acid</th><th class="num">MG/100G</th></tr></thead>
    <tbody>
      <tr><td>Isoleucine</td><td class="num">2980</td></tr>
      <tr><td>Leucine</td><td class="num">2900</td></tr>
      <tr><td>Valine</td><td class="num">3660</td></tr>
      <tr><td>Lysine</td><td class="num">2084</td></tr>
      <tr><td>Methionine</td><td class="num">20466</td></tr>
      <tr><td>Phenylalanine</td><td class="num">2020</td></tr>
      <tr><td>Threonine</td><td class="num">2320</td></tr>
      <tr><td>Tryptophan</td><td class="num">6320</td></tr>
      <tr><td>Alanine</td><td class="num">13265</td></tr>
      <tr><td>Arginine</td><td class="num">6760</td></tr>
      <tr><td>Aspartic Acid</td><td class="num">2480</td></tr>
      <tr><td>Cystine</td><td class="num">3300</td></tr>
      <tr><td>Proline</td><td class="num">7620</td></tr>
      <tr><td>Glutamic</td><td class="num">5520</td></tr>
      <tr><td>Serine</td><td class="num">5900</td></tr>
      <tr><td>Glycine</td><td class="num">1740</td></tr>
      <tr><td>Histidine</td><td class="num">3880</td></tr>
      <tr><td>Tyrosine</td><td class="num">6640</td></tr>
    </tbody>
  </table>
</main>
</body>
</html>
```